Brisk Fixwell business card

I need business card for my business, I think you have all my details.six months ago I design with you car wrap design. We would like to design both side of the card. On front of card we would like logo , Name and our contact details.
At the back we are looking to mentioned our services.
The name will be:
Faridoullan Mestor
Managing Director
Ph:07952338417
Email:info@brisk-fixwell.com
Web:www.brisk-fixwell.com
So we have our logo, you don’t need to change the logo.
Please see the attachment.
Thanks

Target Market(s)

Home improvement

Industry/Entity Type

Home Improvement

Contact Information for Business Card

Company name: Brisk Fixwell
Name: Faridoullan Mestor
Position: Director
Ph:07952338417
Web: www.brisk-fixwell.com
Add: 42 Corvale Road
Hounslow
TW3 9KD
SECOND PERSON
Nizamuddel mestor
Position: Handyman
Ph: 07812 564037
Email: info@brisk-fixwell.com
Add: 18 Brackwin Lane Road
Hounslow
TW6 2LB

```html
<!DOCTYPE html>
<html lang="en">
<head>
<meta charset="utf-8">
<title>Brisk Fixwell – Business Card</title>
<link href="https://fonts.googleapis.com/css2?family=Rubik:wght@500;600&family=Roboto:wght@400&display=swap" rel="stylesheet">
<style>
  :root {
    --page: #dcd8d3;
    --card: #eef0f2;
    --navy: #24286b;
    --red: #e0262b;
    --ink: #2c2c33;
    --tagline: #d6d7e6;
  }
  * { margin: 0; padding: 0; box-sizing: border-box; }
  html, body {
    width: 1200px;
    height: 1054px;
    overflow: hidden;
    background: var(--page);
  }
  .card {
    position: absolute;
    left: 100px;
    top: 225px;
    width: 1000px;
    height: 604px;
    background: var(--card);
    border-radius: 23px;
    overflow: hidden;
    box-shadow: 0 10px 30px rgba(0,0,0,0.12);
  }
  .brand {
    position: absolute;
    left: 74px;
    top: 270px;
    display: flex;
    align-items: center;
    gap: 18px;
  }
  .brand-name {
    font-family: "Rubik", sans-serif;
    font-weight: 600;
    font-size: 58px;
    color: var(--navy);
    letter-spacing: 0.5px;
    line-height: 1;
  }
  .brand-mark {
    width: 20px;
    height: 20px;
    background: var(--red);
  }
  .person {
    position: absolute;
    left: 568px;
    top: 168px;
  }
  .person-name {
    font-family: "Rubik", sans-serif;
    font-weight: 500;
    font-size: 36px;
    color: var(--navy);
    line-height: 1.2;
  }
  .person-title {
    font-family: "Roboto", sans-serif;
    font-size: 25px;
    color: var(--ink);
    margin-top: 6px;
  }
  .contacts {
    position: absolute;
    left: 568px;
    top: 294px;
    list-style: none;
  }
  .contact {
    display: flex;
    align-items: center;
    height: 38.5px;
    font-family: "Roboto", sans-serif;
    font-size: 25px;
    color: var(--ink);
  }
  .contact-icon {
    width: 24px;
    height: 24px;
    margin-right: 26px;
    flex: none;
  }
  .footer-band {
    position: absolute;
    left: 0;
    bottom: 0;
    width: 1000px;
    height: 73px;
    display: block;
  }
  .tagline {
    position: absolute;
    left: 568px;
    bottom: 22px;
    font-family: "Roboto", sans-serif;
    font-size: 24px;
    color: var(--tagline);
  }
</style>
</head>
<body>
  <main class="card">
    <div class="brand">
      <span class="brand-name">Brisk Fixwell</span>
      <span class="brand-mark"></span>
    </div>

    <div class="person">
      <h1 class="person-name">Faridoullan Mestor</h1>
      <p class="person-title">Managing Director</p>
    </div>

    <ul class="contacts">
      <li class="contact">
        <svg class="contact-icon" viewBox="0 0 24 24" aria-hidden="true">
          <path fill="var(--red)" d="M3 9c0-3 3-5 9-5s9 2 9 5v2h-5V8.5c-1.2-.6-2.5-.8-4-.8s-2.8.2-4 .8V11H3z"/>
          <path fill="var(--red)" d="M6 12h12l2 7H4z"/>
          <circle cx="12" cy="15.5" r="2" fill="var(--card)"/>
        </svg>
        <span>07952338417</span>
      </li>
      <li class="contact">
        <svg class="contact-icon" viewBox="0 0 24 24" aria-hidden="true">
          <rect x="2" y="5" width="20" height="14" fill="var(--red)"/>
          <path d="M3 6l9 7 9-7" fill="none" stroke="var(--card)" stroke-width="1.8"/>
        </svg>
        <span>info@brisk-fixwell.com</span>
      </li>
      <li class="contact">
        <svg class="contact-icon" viewBox="0 0 24 24" aria-hidden="true">
          <circle cx="12" cy="12" r="9" fill="var(--red)"/>
          <g fill="none" stroke="var(--card)" stroke-width="1.3">
            <ellipse cx="12" cy="12" rx="4" ry="9"/>
            <path d="M3 12h18M4.5 7.5h15M4.5 16.5h15M12 3v18"/>
          </g>
        </svg>
        <span>www.brisk-fixwell.com</span>
      </li>
    </ul>

    <svg class="footer-band" viewBox="0 0 1000 73" preserveAspectRatio="none" aria-hidden="true">
      <rect x="0" y="51" width="430" height="22" fill="var(--red)"/>
      <path d="M462 0 H1000 V73 H402 L430 16 Q438 0 462 0 Z" fill="var(--navy)"/>
    </svg>
    <p class="tagline">Guarantee Arrival on Time</p>
  </main>
</body>
</html>
```